Accounting firm needing business card / letterhead designed
Marcus L. Trenholm, CPA
marcus@veltrowledger.com
www.veltrowledger.com
842 E Alder Ave Glenmoor, IN 43827
419-562-0974

```html
<!DOCTYPE html>
<html lang="en">
<head>
<meta charset="utf-8">
<title>Veltro Ledger — Business Card</title>
<link rel="stylesheet" href="https://fonts.googleapis.com/css2?family=Roboto:wght@400;700&family=Roboto+Condensed:wght@700&display=swap">
<style>
  :root {
    --navy: #241f5c;
    --green: #84bd3a;
    --paper: #f7f7f7;
    --ink: #3a3a3a;
    --backdrop: #e6e6e6;
    --white: #ffffff;
  }
  * { margin: 0; padding: 0; box-sizing: border-box; }
  html, body { width: 1200px; height: 960px; overflow: hidden; }
  body {
    background: var(--backdrop);
    position: relative;
    font-family: "Roboto", Arial, sans-serif;
  }
  .card { position: absolute; width: 600px; height: 342px; }

  /* Front */
  .card-front { left: 314px; top: 113px; background: var(--paper); }
  .name-band {
    position: absolute; left: 0; top: 45px; width: 304px; height: 70px;
    background: var(--navy);
  }
  .holder-name {
    position: absolute; left: 34px; top: 22px;
    font-family: "Roboto Condensed", Arial, sans-serif;
    font-weight: 700; font-size: 21px; color: var(--green); white-space: nowrap;
  }
  .brand-name {
    position: absolute; right: 36px; top: 62px;
    font-family: "Roboto", Arial, sans-serif; font-weight: 700;
    font-size: 30px; letter-spacing: 1px; color: var(--navy); white-space: nowrap;
  }
  .accent-bar {
    position: absolute; right: 0; top: 45px; width: 26px; height: 70px;
    background: var(--green);
  }
  .contact-list { position: absolute; left: 34px; top: 254px; list-style: none; }
  .contact-list li {
    display: flex; align-items: center; height: 19px;
    font-size: 14.5px; color: var(--ink);
  }
  .contact-list svg { width: 13px; height: 13px; margin-right: 9px; fill: var(--navy); }
  .address {
    position: absolute; right: 34px; top: 274px; text-align: right;
    font-size: 14.5px; line-height: 19px; color: var(--ink);
  }

  /* Back */
  .card-back { left: 311px; top: 472px; background: var(--navy); }
  .back-brand {
    position: absolute; left: 0; right: 0; top: 132px; text-align: center;
    font-family: "Roboto", Arial, sans-serif; font-weight: 700;
    font-size: 42px; letter-spacing: 2px; color: var(--white);
  }
  .back-url {
    position: absolute; left: 0; right: 0; top: 282px; text-align: center;
    font-size: 14px; letter-spacing: 6px; color: var(--white);
  }
</style>
</head>
<body>
  <section class="card card-front">
    <div class="name-band"><p class="holder-name">Marcus L. Trenholm, CPA</p></div>
    <p class="brand-name">VELTRO LEDGER</p>
    <div class="accent-bar"></div>
    <ul class="contact-list">
      <li><svg viewBox="0 0 24 24" aria-hidden="true"><path d="M6.6 10.8a15 15 0 0 0 6.6 6.6l2.2-2.2a1 1 0 0 1 1-.25 11.4 11.4 0 0 0 3.6.57 1 1 0 0 1 1 1V20a1 1 0 0 1-1 1A17 17 0 0 1 3 4a1 1 0 0 1 1-1h3.5a1 1 0 0 1 1 1c0 1.25.2 2.45.57 3.57a1 1 0 0 1-.25 1z"/></svg>555-562-0974</li>
      <li><svg viewBox="0 0 24 24" aria-hidden="true"><path d="M2 5h20v2l-10 6L2 7z"/><path d="M2 9l10 6 10-6v10H2z"/></svg>marcus@veltrowledger.com</li>
      <li><svg viewBox="0 0 24 24" aria-hidden="true"><path d="M12 2a10 10 0 1 0 0 20 10 10 0 0 0 0-20zm-1 17.9A8 8 0 0 1 4.2 10L9 14.8v1a2 2 0 0 0 2 2zm6.9-2.5A2 2 0 0 0 16 16h-1v-3a1 1 0 0 0-1-1H8v-2h2a1 1 0 0 0 1-1V7h2a2 2 0 0 0 2-2v-.4a8 8 0 0 1 2.9 12.8z"/></svg>www.veltrowledger.com</li>
    </ul>
    <p class="address">842 E Alder Ave<br>Glenmoor, IN 43827</p>
  </section>

  <section class="card card-back">
    <p class="back-brand">VELTRO LEDGER</p>
    <p class="back-url">www.veltrowledger.com</p>
  </section>
</body>
</html>
```